Harborline Benches business cards

I’d like a business card design that includes my logo, a tag line and my contact info. Black, textured background. My contact info color should match the orange and blue gradients. Tagline under logo: “Wooden Tables and Furniture of the Highest Quality”

Target Market(s)

High end furniture buyers

Contact Information for Business Card

Contact info, logo and tagline

```html
<!DOCTYPE html>
<html lang="en">
<head>
<meta charset="utf-8">
<title>Harborline Benches business cards</title>
<link href="https://fonts.googleapis.com/css2?family=Poppins:wght@400;500;600&display=swap" rel="stylesheet">
<style>
  :root {
    --backdrop: #979596;
    --paper: #ffffff;
    --charcoal: #202124;
    --brand-blue: #0553a8;
    --brand-orange: #e8732a;
    --white: #ffffff;
  }
  * { box-sizing: border-box; margin: 0; padding: 0; }
  html, body { width: 1075px; height: 1200px; overflow: hidden; }
  body {
    background: var(--backdrop);
    font-family: "Poppins", sans-serif;
    position: relative;
  }
  .card {
    position: absolute;
    left: 206px;
    width: 663px;
    height: 395px;
    overflow: hidden;
    box-shadow: 3px 3px 2px rgba(0,0,0,0.55);
  }
  .card--front { top: 187px; background: var(--paper); }
  .card--back { top: 637px; background: var(--charcoal); }

  .brand-name { position: absolute; font-weight: 500; white-space: nowrap; letter-spacing: -0.3px; }
  .card--front .brand-name {
    right: 42px; top: 88px; font-size: 32px; color: var(--brand-blue);
  }
  .card--back .brand-name {
    left: 0; right: 0; top: 200px; text-align: center; font-size: 48px; color: var(--brand-orange);
  }

  .person { position: absolute; left: 35px; top: 218px; }
  .person__name { font-size: 23px; font-weight: 600; line-height: 1.2; color: var(--brand-blue); }
  .person__name .first { color: var(--brand-orange); }
  .person__title { font-size: 17px; line-height: 1.3; color: var(--brand-blue); }
  .person__rule {
    position: absolute; left: 35px; top: 276px; width: 211px; height: 4px; background: var(--brand-orange);
  }

  .contact-band {
    position: absolute; left: 0; right: 0; top: 279px; bottom: 0; background: var(--brand-blue);
  }
  .contact-list { position: absolute; left: 35px; top: 20px; list-style: none; }
  .contact-list li {
    display: flex; align-items: center; gap: 7px;
    color: var(--white); font-size: 19px; line-height: 23.5px;
  }
  .contact-list svg { width: 17px; height: 17px; flex: none; }
  .address {
    position: absolute; right: 42px; top: 46px; text-align: right;
    color: var(--white); font-size: 19px; line-height: 23.5px; font-style: normal;
  }

  .tagline-band {
    position: absolute; left: 0; right: 0; top: 350px; height: 45px;
    background: var(--brand-orange); display: flex; align-items: center; justify-content: center;
  }
  .tagline { color: var(--white); font-size: 19px; }
</style>
</head>
<body>
  <section class="card card--front">
    <div class="brand-name">Harborline Benches</div>

    <div class="person">
      <div class="person__name"><span class="first">Marcus</span> Ellery</div>
      <div class="person__title">Managing Director</div>
    </div>
    <div class="person__rule"></div>

    <div class="contact-band">
      <ul class="contact-list">
        <li>
          <svg viewBox="0 0 24 24" aria-hidden="true"><path fill="var(--brand-orange)" d="M6.6 10.8a15.1 15.1 0 0 0 6.6 6.6l2.2-2.2c.3-.3.7-.4 1-.2 1.1.4 2.3.6 3.6.6.6 0 1 .4 1 1V20c0 .6-.4 1-1 1A17 17 0 0 1 3 4c0-.6.4-1 1-1h3.5c.6 0 1 .4 1 1 0 1.3.2 2.5.6 3.6.1.3 0 .7-.2 1z"/></svg>
          044-555 018 274
        </li>
        <li>
          <svg viewBox="0 0 24 24" aria-hidden="true"><rect x="2" y="5" width="20" height="14" fill="var(--brand-orange)"/><path d="M2 5l10 8 10-8" fill="none" stroke="var(--brand-blue)" stroke-width="1.6"/></svg>
          hello@harborline.com
        </li>
        <li>
          <svg viewBox="0 0 24 24" aria-hidden="true" fill="none" stroke="var(--brand-orange)" stroke-width="2"><circle cx="12" cy="12" r="9"/><ellipse cx="12" cy="12" rx="4" ry="9"/><path d="M3 12h18M5 7h14M5 17h14"/></svg>
          www.harborline.com
        </li>
      </ul>
      <address class="address">17 Quayside Lane, Dock Row<br>60318, Port Alder</address>
    </div>
  </section>

  <section class="card card--back">
    <div class="brand-name">Harborline Benches</div>
    <div class="tagline-band">
      <p class="tagline">Wooden Tables and Furniture of the Highest Quality</p>
    </div>
  </section>
</body>
</html>
```